Tolvik Commercial Cleaning is lookong for a new business card design.

A fresh new design that's professional and stylish. We need a serious upgrade to our business cards. I have included pictures of our existing ones. Our clients include professional individuals and business owners. We woupdblike something professional and upbeat. Please have fun and see what you come uo with.

Target Market(s)

Property managers, business owners, facility managers and other similar professionals

Industry/Entity Type

Janitorial

Contact Information for Business Card

Name, cell, office number, email, web address

Font styles to use
Sans Serif

Colors

Designer to choose colors to be used in the design.

Requirements
Must have
• please use the green color in our logo
Nice to have
• Bar code
Should not have
• Address

```html
<!DOCTYPE html>
<html lang="en">
<head>
<meta charset="utf-8">
<title>Tolvik Commercial Cleaning – Business Card</title>
<link href="https://fonts.googleapis.com/css2?family=Open+Sans:wght@400;600;700&display=swap" rel="stylesheet">
<style>
  :root {
    --page: #ecebe8;
    --card: #222327;
    --edge: #38b657;
    --green: #38b657;
    --blue: #3a6db0;
    --ghost: #36373b;
    --text: #ffffff;
  }
  * { box-sizing: border-box; margin: 0; padding: 0; }
  html, body { width: 1200px; height: 780px; overflow: hidden; }
  body {
    background: var(--page);
    font-family: "Open Sans", Arial, sans-serif;
    display: flex;
    align-items: center;
    justify-content: center;
    gap: 36px;
  }
  .card {
    position: relative;
    width: 550px;
    height: 314px;
    background: var(--card);
    border-radius: 22px;
    border: 3px solid var(--edge);
    overflow: hidden;
  }
  /* back side */
  .card--back .brand-ghost {
    position: absolute;
    left: 0; right: 0; top: 96px;
    text-align: center;
    color: var(--ghost);
    font-weight: 700;
    font-size: 46px;
    line-height: 1.05;
  }
  /* front side */
  .brand-mark {
    position: absolute;
    left: 34px; top: 34px;
    color: var(--green);
    font-weight: 700;
    font-size: 34px;
    line-height: 1.05;
    width: 260px;
  }
  .front-ghost {
    position: absolute;
    right: 30px; top: 70px;
    color: var(--ghost);
    font-weight: 700;
    font-size: 62px;
    line-height: 1;
  }
  .accent-bar {
    position: absolute;
    right: 0; top: 92px;
    width: 18px; height: 34px;
    background: var(--green);
  }
  .person {
    position: absolute;
    right: 28px; top: 100px;
    font-weight: 700;
    font-size: 26px;
  }
  .person__first { color: var(--green); }
  .person__last { color: var(--blue); }
  .contacts {
    position: absolute;
    left: 34px; bottom: 30px;
    list-style: none;
    color: var(--text);
    font-size: 15px;
    line-height: 1.55;
  }
  .contacts li { display: flex; align-items: center; gap: 10px; }
  .contacts svg { width: 14px; height: 14px; flex: none; }
</style>
</head>
<body>
  <section class="card card--back" aria-label="Card back">
    <div class="brand-ghost">Tolvik<br>Commercial Cleaning</div>
  </section>

  <section class="card card--front" aria-label="Card front">
    <div class="brand-mark">Tolvik Commercial Cleaning</div>
    <div class="front-ghost">Tolvik</div>
    <div class="accent-bar"></div>
    <div class="person"><span class="person__first">Maren</span> <span class="person__last">Coyle</span></div>

    <ul class="contacts">
      <li>
        <svg viewBox="0 0 24 24" fill="var(--green)" aria-hidden="true"><path d="M6.6 10.8a15 15 0 0 0 6.6 6.6l2.2-2.2a1 1 0 0 1 1-.25 11.4 11.4 0 0 0 3.6.57 1 1 0 0 1 1 1V20a1 1 0 0 1-1 1A17 17 0 0 1 3 4a1 1 0 0 1 1-1h3.5a1 1 0 0 1 1 1c0 1.25.2 2.45.57 3.57a1 1 0 0 1-.25 1z"/></svg>
        (555) 014-2290
      </li>
      <li>
        <svg viewBox="0 0 24 24" fill="none" stroke="var(--green)" stroke-width="2.4" aria-hidden="true"><rect x="3" y="5" width="18" height="14" rx="1"/><path d="M3 6l9 7 9-7"/></svg>
        maren@tolvikcleaning.com
      </li>
      <li>
        <svg viewBox="0 0 24 24" fill="none" stroke="var(--green)" stroke-width="2.2" aria-hidden="true"><circle cx="12" cy="12" r="9"/><path d="M3 12h18M12 3c3 3.2 3 14.8 0 18M12 3c-3 3.2-3 14.8 0 18"/></svg>
        www.tolvikcleaning.com
      </li>
    </ul>
  </section>
</body>
</html>
```